** Wanted ** Wordpress web design for scaffolding rental and construction company

We need a website design and must be functional to show a basic overview of what our company offers as a service. We have a domain name and a logo but we need web design. This web site should have another scaffolding rental page for construction and renovation as well as a quote section where customers can enter their personal information and also upload photos. The site% 26quot; www.brindlework.com% 26quot; should be intuitive, clear and classy ... The logo must be found on the site in several ways.

Target Market(s)

Professional and no professional

Coding

Coded - Design and coding required

Number of Pages Required

3 page

Font styles to use
Serif
Sans Serif
Decorative
Script

Requirements
Must have
• Our logo
Nice to have
• Slogan:% 26quot; The height% 26 # 224; port% 26 # 233; e hand% 26quot;

```html
<!DOCTYPE html>
<html lang="en">
<head>
<meta charset="utf-8">
<title>Brindlework — Scaffolding & Construction</title>
<link href="https://fonts.googleapis.com/css2?family=Oswald:wght@500;600&family=Poppins:wght@400;500;600;700&display=swap" rel="stylesheet">
<style>
:root{
  --blue:#0a9be6;
  --dark:#111111;
  --text:#222222;
  --muted:#8d8d8d;
  --line:#e3e3e3;
  --soft:#f3f3f3;
  --white:#ffffff;
}
*{box-sizing:border-box;margin:0;padding:0}
html,body{width:1200px;height:5386px;overflow:hidden;background:var(--white)}
body{position:relative;font-family:"Poppins",sans-serif;color:var(--text)}
.abs{position:absolute}
.photo{position:absolute;display:block}
.head{font-family:"Oswald",sans-serif;font-weight:500;letter-spacing:2px;color:var(--dark)}
.num{font-family:"Oswald",sans-serif;font-weight:600;font-size:44px;color:var(--dark);line-height:1}
.tick{position:absolute;width:4px;height:42px;background:var(--blue)}
.para{font-size:14.5px;line-height:26px;color:var(--muted)}
.btn{position:absolute;background:var(--blue);color:var(--white);font-size:14px;font-weight:500;display:flex;align-items:center;justify-content:center;text-transform:uppercase}
.brand{font-weight:700;color:var(--blue);font-size:18px;letter-spacing:1px;display:flex;align-items:center;gap:10px}
.brand .mark{width:14px;height:14px;background:var(--blue)}

/* top bar */
.topbar{left:477px;top:0;width:723px;height:50px;background:var(--dark);color:var(--white);font-size:15px;display:flex;align-items:center}
.topbar .item{display:flex;align-items:center;gap:10px}
.topbar .social{position:absolute;top:0;height:50px;width:52px;border-left:1px solid #333}
.topbar .social span{position:absolute;left:22px;top:21px;width:8px;height:8px;background:#bbb}
.nav{left:316px;top:86px;display:flex;gap:0;font-size:13.5px;color:#444;text-transform:uppercase}
.nav a{position:absolute;white-space:nowrap;text-decoration:none;color:#444}
.nav a.on{color:var(--blue)}
.search{left:903px;top:77px;width:220px;height:32px;border:1px solid var(--line);border-radius:16px;font-size:12px;color:#aaa;padding:7px 14px}

/* hero */
.hero-card{left:77px;top:213px;width:416px;height:414px;background:var(--white);padding:64px 52px}
.hero-card h1{font-family:"Poppins",sans-serif;font-weight:700;font-size:48px;line-height:58px;color:var(--dark)}

/* services */
.svc{position:absolute;left:77px;width:395px;height:83px;background:var(--soft);border:1px solid var(--line);display:flex;align-items:center;padding-left:22px;gap:22px;font-size:25px;font-weight:500;color:var(--dark)}
.svc.on{background:var(--blue);color:var(--white);border-color:var(--blue)}
.svc svg{width:56px;height:56px}

.caption{position:absolute;color:var(--white);font-size:20px;padding-left:0}
.caption:before{content:"";position:absolute;left:-6px;top:-34px;width:4px;height:40px;background:var(--blue)}
.tag{position:absolute;background:var(--blue);color:var(--white);font-size:13px;font-weight:500;padding:8px 16px;text-transform:uppercase}
.meta{position:absolute;color:var(--white);font-size:13px}

.footer{left:0;top:4904px;width:1200px;height:482px;background:#000;color:var(--white)}
.flinks{position:absolute;left:0;top:5214px;width:1200px;text-align:center;font-size:16px;color:var(--white);word-spacing:6px}
</style>
</head>
<body>

<!-- header -->
<div class="abs brand" style="left:77px;top:62px;height:40px;font-size:19px"><span class="mark"></span>BRINDLEWORK</div>
<div class="abs topbar">
  <div class="item abs" style="left:56px"><svg width="20" height="14" viewBox="0 0 20 14"><rect x="1" y="1" width="18" height="12" fill="none" stroke="#0a9be6" stroke-width="1.6"/><path d="M1 1l9 7 9-7" fill="none" stroke="#0a9be6" stroke-width="1.6"/></svg>info@brindlework.com</div>
  <div class="item abs" style="left:278px;padding-left:30px;border-left:1px solid #333;height:50px"><svg width="18" height="18" viewBox="0 0 24 24"><path d="M5 3l4 0 2 5-3 2c1 3 3 5 6 6l2-3 5 2v4c0 1-1 2-2 2C10 21 3 14 3 5c0-1 1-2 2-2z" fill="none" stroke="#0a9be6" stroke-width="1.8"/></svg>123.456.7890</div>
  <div class="social" style="left:444px"><span></span></div>
  <div class="social" style="left:496px"><span></span></div>
  <div class="social" style="left:548px"><span></span></div>
  <div class="social" style="left:600px;border-right:1px solid #333"><span></span></div>
</div>
<nav class="abs nav">
  <a class="on" style="left:0">Home</a><a style="left:73px">About Us</a><a style="left:171px">Services</a><a style="left:271px">Gallery</a><a style="left:363px">Testimonials</a><a style="left:495px">Contact</a>
</nav>
<div class="abs search">Search Here...<svg class="abs" style="right:12px;top:8px" width="15" height="15" viewBox="0 0 16 16"><circle cx="6.5" cy="6.5" r="5" fill="none" stroke="#777" stroke-width="1.6"/><path d="M10.5 10.5l4 4" stroke="#777" stroke-width="1.6"/></svg></div>

<!-- hero -->
<div class="photo" role="img" aria-label="Engineer in a hard hat working on a laptop at a building site" style="left:314px;top:136px;width:886px;height:571px;background:linear-gradient(135deg,#c9c2b6 0%,#8ea6bf 45%,#6b6256 100%)"></div>
<div class="abs" style="left:0;top:255px;width:77px;height:332px;background:var(--blue)"></div>
<div class="abs hero-card">
  <h1>THE HEIGHT ;<br>PORT</h1>
  <p style="font-size:14.5px;line-height:26px;color:#444;margin-top:16px">Lorem ipsum dolor sit amet, consectetur the adipiscing elit, sed do eiusmod tempor &nbsp;enim ad minim veniam.</p>
</div>
<div class="btn" style="left:130px;top:510px;width:154px;height:50px">Contact Us</div>
<svg class="abs" style="left:178px;top:661px" width="44" height="16" viewBox="0 0 44 16"><path d="M12 2L4 8l8 6z" fill="none" stroke="#0a9be6" stroke-width="1.6"/><path d="M32 2l8 6-8 6z" fill="none" stroke="#0a9be6" stroke-width="1.6"/></svg>

<!-- about -->
<div class="photo" role="img" aria-label="Two site workers in hard hats and safety vests reviewing a clipboard" style="left:0;top:792px;width:573px;height:467px;background:linear-gradient(120deg,#4a4a44 0%,#d88a3a 40%,#c8d24a 75%,#e8e4d8 100%)"></div>
<div class="abs" style="left:416px;top:792px;width:157px;height:157px;background:var(--blue)"></div>
<div class="abs num" style="left:656px;top:793px">01</div>
<div class="tick" style="left:657px;top:853px"></div>
<div class="abs head" style="left:656px;top:905px;font-size:34px">ABOUT US</div>
<p class="abs para" style="left:656px;top:972px;width:470px">Lorem ipsum dolor sit amet, consectetur adipiscing elit, sed do eiusmod tempor incididunt ut labore et dolore magna aliqua. Ut enim ad minim veniam, quis nostrud exercitation ullamclaboris nisi ut aliquip ex ea commodo consequat.</p>
<p class="abs para" style="left:656px;top:1098px;width:470px">Lorem ipsum dolor sit amet, consectetur adipiscing elit, sed do eiusmod tempor incididunt ut labore et dolore magna aliqua. Ut enim ad minim veniam, quis nostrud exercitation.</p>
<div class="btn" style="left:654px;top:1208px;width:155px;height:51px">Learn More</div>

<!-- services -->
<div class="abs num" style="left:79px;top:1347px">02</div>
<div class="abs" style="left:152px;top:1385px;width:40px;height:4px;background:var(--blue)"></div>
<div class="abs head" style="left:215px;top:1348px;font-size:34px">OUR SERVICES</div>
<div class="svc" style="top:1436px"><svg viewBox="0 0 56 56"><rect x="8" y="10" width="40" height="42" fill="none" stroke="#1f2a44" stroke-width="2.5"/><path d="M8 24h40M8 38h40M22 10v42M34 10v42" stroke="#0a9be6" stroke-width="2.5"/></svg>Scaffolding</div>
<div class="svc" style="top:1536px"><svg viewBox="0 0 56 56"><path d="M6 26L28 8l22 18" fill="none" stroke="#1f2a44" stroke-width="2.5"/><rect x="12" y="24" width="32" height="26" fill="none" stroke="#1f2a44" stroke-width="2.5"/><rect x="18" y="30" width="8" height="8" fill="#0a9be6"/><rect x="30" y="30" width="8" height="8" fill="#0a9be6"/></svg>Elevation</div>
<div class="svc on" style="top:1635px"><svg viewBox="0 0 56 56"><path d="M6 28L26 10l20 18" fill="none" stroke="#fff" stroke-width="2.5"/><rect x="12" y="26" width="28" height="24" fill="none" stroke="#fff" stroke-width="2.5"/><path d="M30 48l18-18 4 4-18 18h-4z" fill="none" stroke="#fff" stroke-width="2.5"/></svg>Renovation</div>
<div class="photo" role="img" aria-label="Builder, client and architect studying a blueprint together on site" style="left:539px;top:1344px;width:584px;height:374px;background:linear-gradient(135deg,#9cb8d6 0%,#5b7ea8 45%,#c9b9a2 100%)"></div>
<p class="abs para" style="left:541px;top:1744px;width:584px">Lorem ipsum dolor sit amet, consectetur adipiscing elit, sed do eiusmodtempor incididunt ut labore et dolore magna aliqua. Ut enim ad minim veniam, qnostrud exercitation ullamco laboris nisi ut aliquip commodo consequat.</p>
<a class="abs" style="left:541px;top:1842px;font-size:14.5px;color:var(--blue);text-decoration:underline;font-weight:500">LEARN MORE</a>

<!-- gallery -->
<div class="abs num" style="left:79px;top:1952px">03</div>
<div class="tick" style="left:80px;top:2011px"></div>
<div class="abs head" style="left:79px;top:2063px;font-size:34px">WORK GALLERY</div>
<div class="photo" role="img" aria-label="Large building with steel frame under construction" style="left:77px;top:2145px;width:646px;height:489px;background:linear-gradient(180deg,#c6cfd8 0%,#6d6a66 55%,#9a8a74 100%)"></div>
<div class="caption" style="left:131px;top:2544px">Lorem ipsum dolor sit amet, consectetur.</div>
<div class="btn" style="left:77px;top:2682px;width:186px;height:50px;font-size:14px">View Our Works</div>
<div class="photo" role="img" aria-label="Timber house frame at dusk" style="left:748px;top:1959px;width:375px;height:414px;background:linear-gradient(180deg,#2f5aa0 0%,#4b6fa8 50%,#8d6a44 100%)"></div>
<div class="caption" style="left:801px;top:2284px">Lorem ipsum dolor</div>
<div class="photo" role="img" aria-label="Row of new houses under construction" style="left:748px;top:2400px;width:375px;height:416px;background:linear-gradient(180deg,#b8c0c8 0%,#8e8a82 55%,#6b5a48 100%)"></div>
<div class="caption" style="left:791px;top:2725px">Lorem ipsum dolor</div>

<!-- testimonials -->
<div class="photo" role="img" aria-label="Construction workers in yellow hard hats measuring on site" style="left:0;top:2906px;width:811px;height:372px;background:linear-gradient(120deg,#3a4f6a 0%,#c8a44a 45%,#7d8794 100%)"></div>
<div class="abs num" style="left:886px;top:2910px">04</div>
<div class="tick" style="left:887px;top:2969px"></div>
<div class="abs head" style="left:886px;top:3021px;font-size:34px">TESTIMONIALS</div>
<div class="abs" style="left:311px;top:3104px;width:812px;height:258px;background:var(--white);box-shadow:0 0 14px rgba(0,0,0,.08)"></div>
<div class="photo" role="img" aria-label="Client portrait" style="left:364px;top:3157px;width:121px;height:121px;border-radius:50%;background:linear-gradient(135deg,#6aa8d8,#2c5a88)"></div>
<p class="abs para" style="left:527px;top:3155px;width:560px;font-size:14px">Lorem ipsum dolor sit amet, consectetur adipiscing elit, sed do eiusmod tempor incididunt ut labore et dolore magna aliqua. Ut enim ad minim &nbsp;esse cillum dolore eu fugiat nulla pariatur.</p>
<div class="abs" style="left:521px;top:3250px;font-family:'Oswald',sans-serif;font-size:80px;line-height:1;color:var(--blue)">“</div>
<div class="abs" style="left:600px;top:3258px;font-size:21px;font-weight:500;color:var(--dark)">Client Name</div>
<div class="abs" style="left:600px;top:3292px;font-size:14px;color:#555">Lorem Ipsum</div>
<div class="abs" style="left:1014px;top:3276px;width:26px;height:26px;background:var(--blue)"><svg width="26" height="26" viewBox="0 0 26 26"><path d="M15 8l-5 5 5 5" fill="none" stroke="#fff" stroke-width="2"/></svg></div>
<div class="abs" style="left:1043px;top:3276px;width:26px;height:26px;background:#d8eefb"><svg width="26" height="26" viewBox="0 0 26 26"><path d="M11 8l5 5-5 5" fill="none" stroke="#0a9be6" stroke-width="2"/></svg></div>

<!-- news -->
<div class="abs num" style="left:79px;top:3443px">05</div>
<div class="tick" style="left:80px;top:3502px"></div>
<div class="abs head" style="left:79px;top:3552px;font-size:34px">WHAT'S NEW...?</div>
<div class="photo" role="img" aria-label="Two workers discussing plans on a tablet" style="left:77px;top:3635px;width:646px;height:488px;background:linear-gradient(120deg,#c9a64a 0%,#58606a 45%,#3a4658 100%)"></div>
<div class="tag" style="left:130px;top:3964px">Renovations</div>
<div class="abs" style="left:131px;top:4010px;color:#fff;font-size:20px">Lorem ipsum dolor sit amet, consectetur.</div>
<div class="meta" style="left:131px;top:4048px">February 24, 2020 &nbsp;&nbsp;&nbsp;&nbsp; By | Admin</div>
<div class="photo" role="img" aria-label="Yellow wheel loader in front of city towers" style="left:748px;top:3447px;width:375px;height:416px;background:linear-gradient(180deg,#9aa6b2 0%,#7a7466 50%,#c9a43c 100%)"></div>
<div class="tag" style="left:790px;top:3704px">Renovations</div>
<div class="abs" style="left:791px;top:3754px;color:#fff;font-size:20px">Lorem ipsum dolor sit</div>
<div class="meta" style="left:791px;top:3792px">February 24, 2020 &nbsp;&nbsp;&nbsp; By | Admin</div>
<div class="abs" style="left:748px;top:3888px;width:375px;height:375px;background:var(--soft)"></div>
<div class="abs head" style="left:792px;top:3950px;font-size:34px;line-height:47px">SIGN UP TO OUR<br>NEWSLETTER</div>
<p class="abs para" style="left:792px;top:4062px;width:290px;font-size:14px">Lorem ipsum dolor sit ametconsectetur adipiscing elit, sed do eiusmod.</p>
<div class="abs" style="left:790px;top:4150px;width:287px;height:44px;background:#fff;border:1px solid var(--line);font-size:13px;color:#999;padding:12px 16px">Enter Your Email...</div>
<div class="abs" style="left:1035px;top:4150px;width:42px;height:44px;background:var(--blue)"><svg width="42" height="44" viewBox="0 0 42 44"><path d="M11 22l20-9-6 20-4-8z" fill="none" stroke="#fff" stroke-width="1.8"/></svg></div>
<div class="abs" style="left:80px;top:4164px;width:6px;height:94px;background:var(--blue)"></div>
<div class="abs" style="left:131px;top:4165px;font-size:19px;line-height:32px;font-weight:500;color:var(--dark)">YOU NEED CONSTRUCTION AND RENOVATION<br>SERVICE FOR NEW LOOK?</div>
<div class="abs" style="left:131px;top:4232px;font-size:26px;color:var(--blue)">CALL US NOW ! 123.456.7890</div>

<!-- contact -->
<div class="photo" role="img" aria-label="Construction team gathered over drawings on a site table" style="left:0;top:4354px;width:573px;height:467px;background:linear-gradient(120deg,#5a6068 0%,#c7a060 40%,#bcd24a 80%,#6b7a8a 100%)"></div>
<div class="abs num" style="left:656px;top:4358px">06</div>
<div class="tick" style="left:657px;top:4417px"></div>
<div class="abs head" style="left:656px;top:4470px;font-size:34px">CONTACT US</div>
<svg class="abs" style="left:656px;top:4557px" width="24" height="30" viewBox="0 0 24 30"><path d="M12 28C12 28 3 17 3 11a9 9 0 0118 0c0 6-9 17-9 17z" fill="none" stroke="#0a9be6" stroke-width="2"/><circle cx="12" cy="11" r="3.5" fill="none" stroke="#0a9be6" stroke-width="2"/></svg>
<p class="abs" style="left:709px;top:4552px;font-size:14.5px;line-height:26px;color:#666">123, Address, State Name, Street Name,<br>City Name, Zipcode</p>
<svg class="abs" style="left:656px;top:4627px" width="24" height="30" viewBox="0 0 24 30"><rect x="5" y="2" width="15" height="26" rx="2" fill="none" stroke="#0a9be6" stroke-width="2"/><path d="M10 24h5" stroke="#0a9be6" stroke-width="2"/></svg>
<div class="abs" style="left:709px;top:4630px;font-size:19px;font-weight:500;color:#333">123.456.789</div>
<svg class="abs" style="left:654px;top:4699px" width="28" height="20" viewBox="0 0 28 20"><rect x="2" y="2" width="24" height="16" fill="none" stroke="#0a9be6" stroke-width="2"/><path d="M2 2l12 9 12-9" fill="none" stroke="#0a9be6" stroke-width="2"/></svg>
<div class="abs" style="left:709px;top:4695px;font-size:19px;font-weight:500;color:#333">info@brindlework.com</div>
<div class="abs" style="left:654px;top:4771px;width:50px;height:50px;background:#3b5998"></div>
<div class="abs" style="left:717px;top:4771px;width:50px;height:50px;background:#1da1f2"></div>
<div class="abs" style="left:780px;top:4771px;width:50px;height:50px;background:#0077b5"></div>
<div class="abs" style="left:843px;top:4771px;width:50px;height:50px;background:#dd4b39"></div>

<!-- footer -->
<div class="abs footer"></div>
<div class="abs brand" style="left:0;top:4985px;width:1200px;justify-content:center;font-size:22px"><span class="mark"></span>BRINDLEWORK</div>
<div class="abs" style="left:0;top:5080px;width:1200px;text-align:center;font-size:18px;font-weight:500;color:#fff">Receive important information &amp; updates</div>
<div class="abs" style="left:303px;top:5130px;width:414px;height:50px;background:#fff;font-size:13px;color:#888;padding:16px 14px">Enter Email Address...</div>
<div class="btn" style="left:732px;top:5130px;width:159px;height:50px;font-size:15px">Subscribe Now</div>
<div class="flinks">Home &nbsp;|&nbsp; About Us &nbsp;|&nbsp; Services &nbsp;|&nbsp; Gallery &nbsp;|&nbsp; Testimonials &nbsp;|&nbsp; Contact</div>
<div class="abs" style="left:0;top:5288px;width:1200px;height:1px;background:#222"></div>
<div class="abs" style="left:0;top:5330px;width:1200px;text-align:center;font-size:13px;color:#777">Copyright © BRINDLEWORK - 2020 . All Right Reserved.</div>

</body>
</html>
```